Innovative tech company looking for a new look for business card

We need a business card revamp- our current design is amazingly dated and in need of a new vision. The Delta is logo that is used, but other than that and the company name - we are open to everything- red is the color of choice typically due to delta. QV is a National credit reporting agency servicing lending institutions for more than 24 years.

***We want a minimal, clean design, we want to move away from the harsh- red, black and white feel. The files uploaded are to show what we are currently using and exactly what we want to move AWAY from.

Thanks you to all!

We are looking for a "lighter" feel more "plumwick-esque." We want to move away from the harsh black , white, and red. The files I uploaded were more to show what we currently have and really want to move away from. I am going to edit the brief to be sure this is expressed.

Reason: Still looking for options....

Reason: Still looking for more designs -

```html
<!DOCTYPE html>
<html lang="en">
<head>
<meta charset="utf-8">
<title>Quorvale Ventures – Business Card</title>
<link rel="stylesheet" href="https://fonts.googleapis.com/css2?family=Lato:wght@400;700&display=swap">
<style>
  :root {
    --stage: #e9ebef;
    --brand-blue: #2a4f96;
    --brand-blue-deep: #1f3f80;
    --brand-blue-light: #3a6db3;
    --ink-blue: #223f86;
    --ink-dark: #1c1c24;
    --rule-grey: #9a9a9a;
    --name-grey: #7d7d7d;
    --paper: #ffffff;
  }
  * { box-sizing: border-box; margin: 0; padding: 0; }
  html, body { width: 1200px; height: 680px; overflow: hidden; }
  body {
    background: var(--stage);
    font-family: "Lato", sans-serif;
    display: flex;
    align-items: center;
    justify-content: center;
    gap: 48px;
  }
  .card {
    position: relative;
    width: 540px;
    height: 309px;
    border-radius: 4px;
    overflow: hidden;
    box-shadow: 0 8px 24px rgba(20, 30, 60, 0.18);
  }

  /* Front */
  .card-front { background: var(--paper); }
  .front-brand {
    position: absolute;
    left: 34px; top: 40px; right: 34px;
    display: flex;
    align-items: flex-end;
    gap: 14px;
  }
  .brand-square {
    width: 40px; height: 40px;
    background: var(--brand-blue);
    flex: none;
  }
  .brand-block { flex: 1; }
  .brand-name {
    font-size: 25px;
    font-weight: 400;
    letter-spacing: 0.5px;
    color: var(--name-grey);
    padding-bottom: 6px;
    border-bottom: 1.5px solid var(--rule-grey);
  }
  .person {
    position: absolute;
    left: 46px; top: 128px;
    color: var(--ink-blue);
  }
  .person-name { font-size: 19px; }
  .person-role { font-size: 12px; color: var(--ink-dark); margin-left: 4px; }
  .address {
    position: absolute;
    left: 46px; top: 170px;
    display: flex;
    gap: 10px;
    font-size: 13px;
    line-height: 1.3;
    color: var(--ink-dark);
  }
  .contacts {
    position: absolute;
    right: 38px; top: 128px;
    list-style: none;
    font-size: 12.5px;
    line-height: 1.5;
    color: var(--ink-dark);
  }
  .contacts li { display: flex; align-items: center; gap: 7px; }
  .icon { width: 12px; height: 12px; fill: var(--ink-blue); flex: none; }
  .address .icon { margin-top: 2px; }
  .front-band {
    position: absolute;
    left: 0; bottom: 0;
    width: 540px; height: 62px;
  }
  .band-web {
    position: absolute;
    left: 0; right: 0; bottom: 24px;
    text-align: center;
    color: var(--paper);
    font-size: 14px;
    font-weight: 700;
    letter-spacing: 1.6px;
  }

  /* Back */
  .card-back {
    background: radial-gradient(ellipse at 55% 35%, var(--brand-blue-light), var(--brand-blue) 55%, var(--brand-blue-deep));
    display: flex;
    flex-direction: column;
    align-items: center;
    justify-content: center;
    color: var(--paper);
  }
  .back-name {
    font-size: 30px;
    font-weight: 400;
    letter-spacing: 0.5px;
    padding: 0 6px 8px;
    border-bottom: 1.5px solid rgba(255,255,255,0.55);
  }
  .back-web {
    margin-top: 22px;
    font-size: 14px;
    letter-spacing: 1.6px;
  }
</style>
</head>
<body>
  <section class="card card-front" aria-label="Card front">
    <div class="front-brand">
      <span class="brand-square"></span>
      <div class="brand-block">
        <p class="brand-name">Quorvale Ventures, Inc.</p>
      </div>
    </div>

    <p class="person"><span class="person-name">Marlo Fenwick</span><span class="person-role">Business Analyst</span></p>

    <div class="address">
      <svg class="icon" viewBox="0 0 12 12"><path d="M6 1 0.5 6H2v5h3V8h2v3h3V6h1.5z"/></svg>
      <p>2217 N. Larchmont Way<br>Elmbrook, Ohio<br>USA 44021-3310</p>
    </div>

    <ul class="contacts">
      <li><svg class="icon" viewBox="0 0 12 12"><path d="M2.5 1h2l1 2.5-1.3 1a6 6 0 0 0 3.3 3.3l1-1.3L11 7.5v2A1.5 1.5 0 0 1 9.5 11 8.5 8.5 0 0 1 1 2.5 1.5 1.5 0 0 1 2.5 1z"/></svg>Direct 555 014 2080</li>
      <li><svg class="icon" viewBox="0 0 12 12"><path d="M3 1h6v3H3zM1 5h10v5H9V8H3v2H1zM3 9h6v2H3z"/></svg>Direct 555 014 2180</li>
      <li><svg class="icon" viewBox="0 0 12 12"><path d="M1 3h10v6H1zM1.5 3.5 6 7l4.5-3.5" stroke="#fff" stroke-width="0.8"/></svg>info@QuorvaleVentures.com</li>
    </ul>

    <svg class="front-band" viewBox="0 0 540 62" preserveAspectRatio="none" aria-hidden="true">
      <path d="M0 62V36Q0 20 18 20H522Q540 20 540 4V62z" fill="var(--brand-blue)"/>
    </svg>
    <p class="band-web">www.QuorvaleVentures.com</p>
  </section>

  <section class="card card-back" aria-label="Card back">
    <p class="back-name">Quorvale Ventures, Inc.</p>
    <p class="back-web">www.QuorvaleVentures.com</p>
  </section>
</body>
</html>
```